Pull Up Banner - Recruitment Company

We would like a design for a pull up banner.

For context: we are a recruitment business. We specialise in helping people in healthcare industry to find jobs in Australia.

I have come up with several ideas and text for the banner. Feel free to use the following as you see appropriate:

- Our logo (see attached)
- 'Healthcare Recruitment Agency'
- Some sort of imagine / cartoon of medical professionals (ie. doctor, nurse, physiotherapist, speech pathologist). A cartoon is more friendly than committing to a photo
- 'Empowering your next career move'
- 'Discover tailored opportunities based on your career preferences'
- Dot points (allied health, nursing, medical imaging)
- Contact info at the bottom including our website (www.quellastaffing.com.au, our Instagram handle @quellastaffing, Mobile: XXXX XXX XXX. The title section for contact information could be 'Get in touch:'

Feel free to submit a couple of designs and we can merge aspects that look good on your designs and find the perfect fit.
Thank you
Updates

Hello,

Thank you for your initial submissions to this project. I appreciate the time you've invested.

After reviewing the first attempt, I'd like to share some feedback and initial observations:

- Professionalism and engagement: Is the overall appearance of the banner professional? It's crucial that we have a high-quality design as this will represent our business.

- Image selection: The image (whether cartoon or real people) appears quite generic. Please consider submitting the banner with a few different photos in the middle for us to choose from. Ensure the image is a good fit and not simply a generic stock photo.

- Contact section: Kindly remove the phone number; we no longer wish to include it on the banner. Instead, please include our website (www.quellastaffing.com.au) and Instagram handle (@quellastaffing).

- Color scheme: White, black, and red/pink are preferred, or alternatively, blue. However, please avoid incorporating too many different colors as it may detract from the professional appearance.

We will be printing the design on a banner and require it to look professional and engaging.

Thank you once again for your submissions. I hope the feedback provided above is helpful.

Warm regards,

Target Market(s)

Allied Health Australia

Font styles to use
Serif

Colors
0054AA
0677BA
7BADD7
CADEEF
E8F1F8
0094D4
00A9DD
6FCCEA
C7EBF8
E9F6FB
EB3D1F
EC4F4E
F09395
F8D3D4
FCEDEE

```html
<!DOCTYPE html>
<html lang="en">
<head>
<meta charset="utf-8">
<title>Quella Staffing – Pull Up Banner</title>
<link href="https://fonts.googleapis.com/css2?family=Poppins:wght@400;600;700;800&display=swap" rel="stylesheet">
<style>
  :root {
    --page-bg: #ededed;
    --banner-white: #ffffff;
    --ink: #161616;
    --panel-dark: #1f1f1f;
    --brand-blue: #3a70ae;
    --accent-blue: #3c7dc4;
    --pill-blue: #4785cc;
    --soft-blue: #cadeef;
    --pale-blue: #e8f1f8;
    --mid-blue: #7badd7;
    --icon-red: #ec4f4e;
    --text-light: #ffffff;
  }
  * { margin: 0; padding: 0; box-sizing: border-box; }
  html, body {
    width: 800px; height: 1200px; overflow: hidden;
    background: var(--page-bg);
    font-family: "Poppins", sans-serif;
  }
  .banner {
    position: absolute; left: 145px; top: 0;
    width: 510px; height: 1200px;
    background: var(--banner-white);
    overflow: hidden;
    box-shadow: 0 0 18px rgba(0,0,0,0.25);
  }
  .banner-shapes, .hospital-scene { position: absolute; left: 0; top: 0; }
  .brand {
    position: absolute; left: 0; right: 0; top: 60px;
    text-align: center;
  }
  .brand-name {
    font-weight: 700; font-size: 33px; letter-spacing: 4px;
    color: var(--ink); line-height: 1;
  }
  .brand-rule {
    display: inline-block; width: 117px; height: 8px;
    background: var(--ink); margin-top: 10px;
  }
  .headline {
    position: absolute; left: 0; right: 0; top: 156px;
    text-align: center; font-weight: 700; line-height: 0.86;
  }
  .headline-blue {
    display: block; color: var(--brand-blue);
    font-size: 62px; letter-spacing: -1.8px;
  }
  .headline-dark {
    display: block; color: var(--ink);
    font-size: 88px; letter-spacing: -3px; margin-top: 2px;
  }
  .tagline {
    position: absolute; left: 0; right: 0; top: 348px;
    text-align: center; color: var(--ink);
    font-weight: 700; font-size: 28px; line-height: 34px; letter-spacing: -0.5px;
  }
  .discover {
    position: absolute; left: 48px; top: 834px; width: 200px;
    color: var(--text-light); font-size: 20.5px; line-height: 26px;
  }
  .discover-title {
    display: block; color: var(--accent-blue);
    font-weight: 700; font-size: 22px; line-height: 26px;
  }
  .specialties {
    position: absolute; left: 291px; top: 845px; list-style: none;
  }
  .specialty {
    display: flex; align-items: center; height: 53px;
    color: var(--text-light); font-weight: 700; font-size: 15.5px;
  }
  .specialty-badge {
    width: 45px; height: 45px; border-radius: 50%;
    border: 4px solid var(--accent-blue);
    background: var(--banner-white);
    box-shadow: inset 0 0 0 3px var(--pale-blue);
    margin-right: 13px; flex: none;
    display: flex; align-items: center; justify-content: center;
  }
  .specialty-icon { width: 22px; height: 22px; }
  .cta {
    position: absolute; left: 101px; top: 1029px;
    width: 307px; height: 46px; border-radius: 23px;
    background: var(--pill-blue);
    border: 4px solid var(--banner-white);
    color: var(--text-light); text-align: center;
    font-weight: 700; font-size: 31px; line-height: 38px; letter-spacing: -0.5px;
  }
  .social {
    position: absolute; left: 0; right: 0; top: 1089px;
    display: flex; justify-content: center; align-items: center;
    color: var(--ink); font-weight: 700; font-size: 18px;
  }
  .social-mark {
    width: 15px; height: 15px; border-radius: 4px;
    background: var(--pill-blue); margin-right: 6px;
  }
  .website {
    position: absolute; left: 0; right: 0; top: 1126px;
    text-align: center; color: var(--ink);
    font-weight: 700; font-size: 17px; letter-spacing: 5.2px;
  }
  .website-name { color: var(--accent-blue); }
</style>
</head>
<body>
  <main class="banner">
    <svg class="banner-shapes" viewBox="0 0 510 1200" width="510" height="1200" aria-hidden="true">
      <defs>
        <linearGradient id="sceneFade" x1="0" y1="0" x2="0" y2="1">
          <stop offset="0" stop-color="#ffffff"/>
          <stop offset="0.45" stop-color="#f1f2f4"/>
          <stop offset="1" stop-color="#e9ecef"/>
        </linearGradient>
      </defs>
      <rect class="backdrop-fade" x="0" y="410" width="510" height="400" fill="url(#sceneFade)"/>
      <path class="panel-left" d="M0 691 L195 804 Q250 830 250 880 L250 1054 L0 1054 Z" fill="#1f1f1f"/>
      <path class="panel-right" d="M510 691 L319 804 Q263 830 263 880 L263 1054 L510 1054 Z" fill="#1f1f1f"/>
    </svg>

    <svg class="hospital-scene" viewBox="0 0 510 1200" width="510" height="1200"
         role="img" aria-label="Isometric illustration of a hospital ward with staff at a reception desk, filing cabinets and a patient in bed">
      <defs>
        <linearGradient id="sceneTone" x1="0" y1="0" x2="0.6" y2="1">
          <stop offset="0" stop-color="#cadeef"/>
          <stop offset="0.55" stop-color="#a7c8e8"/>
          <stop offset="1" stop-color="#6f9fd0"/>
        </linearGradient>
      </defs>
      <path d="M255 440 L470 560 L470 650 L262 800 Q255 806 246 800 L40 668 L40 585 Z" fill="url(#sceneTone)"/>
    </svg>

    <header class="brand">
      <div class="brand-name">QUELLA STAFFING</div>
      <span class="brand-rule"></span>
    </header>

    <h1 class="headline">
      <span class="headline-blue">HEALTHCARE</span>
      <span class="headline-blue">RECRUITMENT</span>
      <span class="headline-dark">AGENCY</span>
    </h1>

    <p class="tagline">Empowering your next<br>career move</p>

    <p class="discover">
      <span class="discover-title">DISCOVER</span>
      Tailored opportunities based on your career preferences
    </p>

    <ul class="specialties">
      <li class="specialty">
        <span class="specialty-badge">
          <svg class="specialty-icon" viewBox="0 0 24 24" aria-hidden="true">
            <path d="M12 21 L3.5 12.5 A5 5 0 0 1 12 5.5 A5 5 0 0 1 20.5 12.5 Z" fill="#ec4f4e"/>
            <path d="M5 12 H9 L10.5 9 L13 15 L14.5 12 H19" fill="none" stroke="#ffffff" stroke-width="1.6" stroke-linejoin="round"/>
          </svg>
        </span>Allied health
      </li>
      <li class="specialty">
        <span class="specialty-badge">
          <svg class="specialty-icon" viewBox="0 0 24 24" aria-hidden="true">
            <rect x="3" y="3" width="18" height="18" rx="4" fill="#3c7dc4"/>
            <path d="M12 7 V17 M7 12 H17" stroke="#ffffff" stroke-width="3" stroke-linecap="round"/>
          </svg>
        </span>Nursing
      </li>
      <li class="specialty">
        <span class="specialty-badge">
          <svg class="specialty-icon" viewBox="0 0 24 24" aria-hidden="true">
            <path d="M12 20 L3.5 11.5 A5 5 0 0 1 12 4.5 A5 5 0 0 1 20.5 11.5 Z" fill="#ec4f4e"/>
            <path d="M12 8.5 V14.5 M9 11.5 H15" stroke="#ffffff" stroke-width="2.2" stroke-linecap="round"/>
          </svg>
        </span>Medical
      </li>
    </ul>

    <div class="cta">GET IN TOUCH</div>

    <p class="social"><span class="social-mark"></span>@quellastaffing</p>
    <p class="website">www.<span class="website-name">quellastaffing</span>.com.au</p>
  </main>
</body>
</html>
```